R7M Horizon Business Card Design

We need a business card created for our New Business "R7M Horizon"<br/><br/>The business card design is up to you however the following information must be on the business card:<br/><br/>Front of the business card -<br/>Email :darrenp@r7mhorizon.nz<br/>Mobile: +64 (0) 22 4870 619<br/>Website: www.r7mhorizon.nz<br/>Card Owner Name: Darren Paltrow<br/>Company Title: Business Development Manager<br/>Slogan: "The BEST of both worlds". <br/>Logo On the front attached to the design brief<br/><br/>On the back: <br/>Space on the back for 4 more versions of the logo across the bottom of the card indicating different subsidiary brands - R7M Coffee, R7M Arts, R7M ?? (The card will be used for all of these brands - We Will add the extra subsidiary logos to the design once the design is finished (We are a graphics design team). <br/><br/>Other than that we want a premium feeling logo that remains universally usable depending on the business entity that we are using the card for. The use of bright bold colours would be great but we still want the card to feel premium.
Target Market(s)
Gift Design and Manufacturing Companies
Contact Information for Business Card
Front of the business card -
Email :darrenp@r7mhorizon.nz
Mobile: +64 (0) 22 4870 619
Website: www.r7mhorizon.nz
Card Owner Name: Darren Paltrow
Company Title: Business Development Manager
Slogan: "The BEST of both worlds".
Logo On the front attached to the design brief

```html
<!DOCTYPE html>
<html lang="en">
<head>
<meta charset="utf-8">
<title>R7M Horizon Business Card</title>
<link href="https://fonts.googleapis.com/css2?family=Michroma&family=Open+Sans:wght@400;600&family=Saira:wght@400;700&display=swap" rel="stylesheet">
<style>
  :root {
    --brand-blue: #3445a0;
    --brand-blue-light: #4553a8;
    --card-white: #ffffff;
    --ink-dark: #222228;
    --stage: #2a2a2c;
  }
  html, body {
    margin: 0;
    padding: 0;
    width: 1200px;
    height: 900px;
    overflow: hidden;
    background: var(--stage);
  }
  .stage {
    position: relative;
    width: 1200px;
    height: 900px;
  }
  .card {
    position: absolute;
    left: 290px;
    width: 620px;
    height: 354px;
    border-radius: 18px;
    overflow: hidden;
    box-shadow: 0 10px 30px rgba(0,0,0,0.45);
  }
  .brand-name {
    font-family: 'Michroma', sans-serif;
    white-space: nowrap;
    line-height: 1;
  }
  .brand-dot {
    flex: none;
    border-radius: 50%;
  }

  /* Back side */
  .card-back {
    top: 64px;
    background: linear-gradient(120deg, var(--brand-blue) 0%, var(--brand-blue) 45%, var(--brand-blue-light) 100%);
    color: var(--card-white);
  }
  .back-brand {
    position: absolute;
    left: 0;
    right: 0;
    top: 128px;
    display: flex;
    justify-content: center;
    align-items: center;
    gap: 16px;
  }
  .back-brand .brand-name {
    font-size: 34px;
    color: var(--card-white);
  }
  .back-brand .brand-dot {
    width: 20px;
    height: 20px;
    background: var(--card-white);
  }
  .slogan {
    margin: 0;
    font-family: 'Saira', sans-serif;
    font-weight: 400;
    display: flex;
    align-items: center;
    gap: 8px;
    white-space: nowrap;
  }
  .slogan strong { font-weight: 700; }
  .card-back .slogan {
    position: absolute;
    left: 0;
    right: 0;
    bottom: 90px;
    justify-content: center;
    font-size: 19px;
    color: var(--card-white);
  }
  .arrow { width: 11px; height: 11px; fill: currentColor; }

  /* Front side */
  .card-front {
    top: 474px;
    background: var(--card-white);
  }
  .holder-name {
    position: absolute;
    left: 40px;
    top: 40px;
    margin: 0;
    font-family: 'Michroma', sans-serif;
    font-size: 27px;
    font-weight: 400;
    letter-spacing: 1px;
    white-space: nowrap;
    color: var(--brand-blue);
    -webkit-text-stroke: 0.8px var(--brand-blue);
  }
  .holder-title {
    position: absolute;
    left: 40px;
    top: 84px;
    margin: 0;
    font-family: 'Open Sans', sans-serif;
    font-size: 16px;
    color: var(--ink-dark);
  }
  .card-front .slogan {
    position: absolute;
    left: 48px;
    top: 168px;
    font-size: 18px;
    color: var(--brand-blue);
  }
  .contact-list {
    position: absolute;
    left: 40px;
    top: 216px;
    margin: 0;
    padding: 0;
    list-style: none;
    font-family: 'Open Sans', sans-serif;
    font-size: 18px;
    color: var(--ink-dark);
  }
  .contact-list li {
    display: flex;
    align-items: center;
    gap: 12px;
    height: 30px;
    white-space: nowrap;
  }
  .contact-icon {
    width: 15px;
    height: 15px;
    fill: none;
    stroke: var(--brand-blue);
    stroke-width: 1.6;
  }
  .front-brand {
    position: absolute;
    right: 36px;
    top: 200px;
    display: flex;
    align-items: center;
    gap: 12px;
  }
  .front-brand .brand-name {
    font-size: 22px;
    color: var(--brand-blue);
  }
  .front-brand .brand-dot {
    width: 16px;
    height: 16px;
    background: var(--brand-blue);
  }
</style>
</head>
<body>
<main class="stage">

  <section class="card card-back" aria-label="Card back">
    <div class="back-brand">
      <span class="brand-name">R7M Horizon</span>
      <span class="brand-dot"></span>
    </div>
    <p class="slogan">
      <svg class="arrow" viewBox="0 0 10 10"><polygon points="10,0 10,10 0,5"/></svg>
      <span>The <strong>BEST</strong> of both worlds</span>
      <svg class="arrow" viewBox="0 0 10 10"><polygon points="0,0 0,10 10,5"/></svg>
    </p>
  </section>

  <section class="card card-front" aria-label="Card front">
    <h1 class="holder-name">DARREN PALTROW</h1>
    <p class="holder-title">Business Development Manager</p>

    <p class="slogan">
      <svg class="arrow" viewBox="0 0 10 10"><polygon points="0,0 0,10 10,5"/></svg>
      <span>The <strong>BEST</strong> of both worlds</span>
    </p>

    <ul class="contact-list">
      <li>
        <svg class="contact-icon" viewBox="0 0 16 16"><path d="M4 1.5 L6.5 4.5 L5 6.5 Q6.5 9.5 9.5 11 L11.5 9.5 L14.5 12 L13 14.5 Q6 14 1.5 3 Z"/></svg>
        <span>+64 (0) 22 4870 619</span>
      </li>
      <li>
        <svg class="contact-icon" viewBox="0 0 16 16"><rect x="1.5" y="3.5" width="13" height="9"/><polyline points="1.5,3.5 8,9 14.5,3.5"/></svg>
        <span>darrenp@r7mhorizon.nz</span>
      </li>
      <li>
        <svg class="contact-icon" viewBox="0 0 16 16"><circle cx="8" cy="8" r="6.5"/><ellipse cx="8" cy="8" rx="3" ry="6.5"/><line x1="1.5" y1="8" x2="14.5" y2="8"/></svg>
        <span>www.r7mhorizon.nz</span>
      </li>
    </ul>

    <div class="front-brand">
      <span class="brand-name">R7M Horizon</span>
      <span class="brand-dot"></span>
    </div>
  </section>

</main>
</body>
</html>
```